Luxury Wine Label for New Startup Winery

We need a wine label for our new winery startup. We have worked with a local designer but do not feel the resulting label / logo have the elevation required to present our brand as a luxury wine. Our winery is called "Quailbrook Vineyards" and we are focused on extremely high quality hand crafted artisan and estate wines from the Pacific Northwest.
We would like to see designs that utilize a tree line, or other imagery that represents the "Quailbrook" part of our company name. Another interesting feature could be wood grain.
A logo will be required based on your design so please design with this in mind:
This logo should be consistent with the wine bottle label design, and should be representative of our high end exclusive wine while giving a sense of place (Oregon/ Pacific Northwest.)
I will supply an image of the design we received from our local designer, PLEASE NOTE: in general we do like wood grain and tree line concepts but feel the execution was poorly done.
ATTN: Logo design should be suitable for use on: Bottles (Red wine/rose/white wine), Bussiness cards, vehicle signage, business signage, etc
P.S.:
If you have a design that is not outside the box we are still interested in seeing it.
Label is for a burgundy style bottle with a label height of 3.5 - 4" and a width of 3.5-4"
any label <= 4"x4" and >=3.5"x3.5" will be acceptable:
HOWEVER Width should be greater than or equal to height due to the bottle format
Target Market(s)
Wine enthusiasts with adequate discretionary budgets to afford $100 bottles of wine.
Industry/Entity Type
Wine / Winery
Requirements
Must have
- A sense of luxury, a feel of exclusivity, and a theme consistent with our product and brand name
Nice to have
- Tree line, wood grain or other wood themes. Serif fonts
Should not have
- anything cheesy, off topic, hard to read script fonts or anything that makes the label hard to read from a few feet away or too busy

```html
<!DOCTYPE html>
<html lang="en">
<head>
<meta charset="UTF-8">
<title>Quailbrook Vineyards – Syrah Label</title>
<link href="https://fonts.googleapis.com/css2?family=Jost:wght@400;500;600&display=swap" rel="stylesheet">
<style>
  :root {
    --backdrop: #e4e4e4;
    --wood-dark: #2a1a10;
    --wood-mid: #4a3020;
    --wood-light: #5d3d28;
    --linen: #ecebe8;
    --linen-shade: #dcdbd7;
    --snow: #f4f4f2;
    --seal-gold: #d08f2c;
    --seal-light: #eaa83f;
    --ink-light: #f1efea;
    --ink-dark: #2a2622;
  }
  * { margin: 0; padding: 0; box-sizing: border-box; }
  html, body {
    width: 1200px; height: 1200px; overflow: hidden;
    background: var(--backdrop);
    font-family: "Jost", sans-serif;
  }
  .label {
    position: absolute; left: 170px; top: 290px;
    width: 860px; height: 820px;
    background: var(--linen);
    box-shadow: 0 10px 30px rgba(0,0,0,0.18);
  }
  .wood-panel {
    position: absolute; left: 0; top: 0; width: 100%; height: 540px;
    background: linear-gradient(90deg, var(--wood-dark) 0%, var(--wood-mid) 20%, var(--wood-light) 45%, var(--wood-mid) 70%, var(--wood-dark) 100%);
  }
  .treeline {
    position: absolute; left: 0; top: 400px; width: 100%; height: 160px;
    background: linear-gradient(180deg, rgba(244,244,242,0) 0%, rgba(244,244,242,0.4) 45%, var(--snow) 85%, var(--linen) 100%);
  }
  .linen-panel {
    position: absolute; left: 0; top: 560px; width: 100%; height: 260px;
    background: linear-gradient(180deg, var(--linen) 0%, var(--linen-shade) 100%);
  }
  .seal {
    position: absolute; left: 50%; top: -90px;
    width: 290px; height: 290px; margin-left: -145px;
    border-radius: 50%;
    background: radial-gradient(circle at 40% 35%, var(--seal-light), var(--seal-gold) 70%);
  }
  .brand-name, .brand-sub, .varietal, .appellation, .vintage {
    position: absolute; left: 0; width: 100%; text-align: center; line-height: 1;
  }
  .brand-name {
    top: 250px; font-size: 90px; font-weight: 500;
    letter-spacing: 4px; color: var(--ink-light);
  }
  .brand-sub {
    top: 350px; font-size: 48px; font-weight: 400;
    letter-spacing: 14px; color: var(--ink-light);
  }
  .varietal {
    top: 590px; font-size: 104px; font-weight: 600;
    letter-spacing: 20px; color: var(--ink-dark);
  }
  .appellation {
    top: 722px; font-size: 34px; font-weight: 400;
    letter-spacing: 2px; color: var(--ink-dark);
  }
  .vintage {
    top: 766px; font-size: 34px; font-weight: 400;
    letter-spacing: 3px; color: var(--ink-dark);
  }
</style>
</head>
<body>
  <div class="label">
    <div class="wood-panel" role="img" aria-label="Dark vertical wood grain planks"></div>
    <div class="treeline" role="img" aria-label="White silhouette of an evergreen tree line"></div>
    <div class="linen-panel" role="img" aria-label="Light linen textured paper"></div>
    <div class="seal" aria-hidden="true"></div>
    <div class="brand-name">QUAILBROOK</div>
    <div class="brand-sub">VINEYARDS</div>
    <div class="varietal">SYRAH</div>
    <div class="appellation">WILLAMETTE VALLEY</div>
    <div class="vintage">2024</div>
  </div>
</body>
</html>
```